Web Site Mock Up's for a Dog Food Business

We are a supplier of bespoke dog food. We tailor our dog food to meet the dogs needs.We are looking for ideas (mock ups) of design ideas for our new web site - Just mock ups - web site will follow if we are happy with the mock ups.I have included our logo (PSD file). I have also included a rough (please don’t copy) home page with the information we would ideally like on the page. Note the page will have sliders at the top, we have done two example sliders, and included a video to be included.I have also enclosed the questions we need to find out in order to develop a dogs food.I would like to see a home page, and a tell us about your dog page.Would like mock ups as PSD files, so we can play around with.I am open to ideas and better designs. DO NOT JUST COPY MY LAYOUTSome of our competitors sites include www.tails.comwww.paws.comwww.parcelpet.comwww.growlingtums.co.ukI want a clean, bright easy to navigate site. Happy to play around with colours - doesn’t have to be the browns I have used. Happy to use both infographics and photo of real dogs, but I do want site to look like the best food available for dogs.Web site will be a database driven site, with around 10 -15 pages plus about 60 dynamic database driven pages of products (all same layout )Look forward to receiving your ideas.

```html
<!DOCTYPE html>
<html lang="en">
<head>
<meta charset="utf-8">
<title>Barkfeast – Bespoke Dog Food</title>
<link href="https://fonts.googleapis.com/css2?family=Lato:wght@400;700;900&display=swap" rel="stylesheet">
<style>
:root{
  --orange:#e8912c;
  --brown:#4a2a18;
  --red:#d0312d;
  --ink:#2a2a2a;
  --text:#555;
  --light:#f1f1f1;
  --line:#dcdcdc;
  --footer:#2b2b2b;
  --white:#fff;
  --kibble:#b86a2e;
}
*{box-sizing:border-box;margin:0;padding:0}
html,body{width:1200px;height:5202px;overflow:hidden}
body{font-family:'Lato',sans-serif;color:var(--text);background:var(--white);position:relative}
.section{position:absolute;left:0;width:1200px}
.btn{display:inline-block;font-weight:700;font-size:15px;padding:7px 22px;border:2px solid var(--orange);color:var(--ink);background:var(--white)}
.btn-solid{background:var(--orange);color:var(--white);border-color:var(--orange)}

/* header */
.site-header{top:0;height:115px;display:flex;align-items:center;padding:0 76px}
.brand{display:flex;align-items:center;gap:10px;font-weight:900;font-size:22px;color:var(--red)}
.brand-dot{width:22px;height:22px;border-radius:50%;background:var(--red)}
.main-nav{margin-left:auto;display:flex;align-items:center;gap:28px;font-size:13px;font-weight:700;color:var(--ink);text-transform:uppercase}
.main-nav .active{color:var(--red)}
.login{background:var(--brown);color:var(--white);padding:8px 24px;border-radius:18px}

/* hero */
.hero{top:115px;height:595px;text-align:center;color:var(--white);overflow:hidden}
.hero-photo{position:absolute;inset:0;background:linear-gradient(180deg,#a9a9a9 0%,#8e8e8e 50%,#7a7a7a 100%)}
.hero h1{position:absolute;top:195px;left:0;right:0;font-size:38px;font-weight:900;line-height:1.3;text-transform:uppercase;letter-spacing:.5px}
.hero .btn-solid{position:absolute;top:330px;left:50%;transform:translateX(-50%);font-size:22px;padding:12px 40px;border-radius:30px;text-transform:uppercase;white-space:nowrap}
.play{position:absolute;top:420px;left:50%;transform:translateX(-50%);display:flex;align-items:center;gap:10px;font-size:14px;font-weight:700;text-transform:uppercase;white-space:nowrap}
.dots{position:absolute;top:540px;left:50%;transform:translateX(-50%);display:flex;gap:8px}
.dots span{width:10px;height:10px;border-radius:50%;background:var(--white)}
.dots span:first-child{background:var(--red)}

/* how it works */
.how{top:710px;height:435px;text-align:center}
.section-title{font-size:28px;font-weight:900;color:var(--ink);text-transform:uppercase}
.how .section-title{margin-top:58px}
.steps{display:flex;justify-content:space-between;padding:0 90px;margin-top:42px}
.step{width:300px}
.step h3{font-size:21px;font-weight:900;color:var(--ink);margin:16px 0 10px}
.step p{font-size:13px;line-height:1.6}

/* food rows */
.food-row{height:339px;display:flex;align-items:center;padding:0 76px}
.food-row.grey{background:var(--light)}
.food-photo{width:507px;height:246px;border:5px solid var(--white);box-shadow:0 2px 8px rgba(0,0,0,.3);flex:none}
.food-text{width:507px;margin-left:34px}
.food-row.reverse{flex-direction:row-reverse;justify-content:flex-end}
.food-row.reverse .food-text{margin-left:0;margin-right:34px}
.food-text h2{font-size:28px;font-weight:900;color:var(--ink);margin-bottom:18px}
.food-text p{font-size:14px;line-height:1.7;margin-bottom:10px}
.food-text .btn{margin-top:8px}

/* testimonials */
.reviews{top:3513px;height:631px;text-align:center}
.reviews .section-title{margin-top:50px}
.kibble{position:absolute;right:0;top:0;width:220px;height:170px;background:linear-gradient(200deg,#a85a24 0%,#c9864c 45%,rgba(255,255,255,0) 85%)}
.review-card{position:absolute;left:253px;top:118px;width:690px;height:364px;border:1px solid var(--line);background:var(--white)}
.avatar{width:166px;height:166px;border-radius:50%;background:linear-gradient(#d8c2a8,#b08a66);margin:14px auto 0;border:4px solid var(--white);box-shadow:0 0 0 1px var(--line)}
.review-card blockquote{font-size:17px;line-height:1.6;color:var(--ink);margin:30px 70px 10px}
.review-card cite{font-style:normal;font-size:13px;font-weight:700;color:var(--orange);text-transform:uppercase}
.arrow{position:absolute;top:290px}
.reviews .btn{position:absolute;top:548px;left:50%;transform:translateX(-50%);white-space:nowrap}

/* faq */
.faq{top:4144px;height:468px;background:var(--light)}
.faq .section-title{text-align:center;margin-top:44px}
.faq-list{position:absolute;left:166px;top:110px;width:867px;list-style:none}
.faq-list li{height:46px;background:var(--white);margin-bottom:13px;display:flex;align-items:center;justify-content:space-between;padding:0 20px;font-size:13px;color:var(--ink)}

/* contact */
.contact{top:4612px;height:427px;overflow:hidden}
.contact .section-title{text-align:center;margin-top:30px}
.contact-kibble{position:absolute;left:0;top:0;width:200px;height:200px;background:linear-gradient(160deg,#b06a34 0%,#cf9a66 45%,rgba(255,255,255,0) 85%)}
.contact-dog{position:absolute;right:0;bottom:0;width:240px;height:200px;background:linear-gradient(20deg,#c93a34 0%,#6a6a6a 35%,#d8d8d8 70%,rgba(255,255,255,0) 95%)}
.contact-form{position:absolute;left:253px;top:106px;width:694px}
.field-row{display:flex;justify-content:space-between;margin-bottom:13px}
.field{width:335px;height:41px;border:1px solid #bdbdbd;font-size:12px;color:#777;padding:13px 12px;background:var(--white)}
.field.message{width:100%;height:104px}
.contact-form .btn-solid{display:block;width:208px;margin:50px auto 0;text-align:center;font-size:15px;padding:12px 0;text-transform:uppercase}

/* footer */
.site-footer{top:5039px;height:163px;background:var(--footer);color:var(--white);text-align:center}
.footer-nav{display:flex;justify-content:center;gap:26px;font-size:12px;font-weight:700;text-transform:uppercase;margin-top:42px}
.copyright{font-size:11px;color:#bbb;margin-top:12px}
.social{display:flex;justify-content:center;gap:18px;margin-top:22px}
.social span{width:16px;height:16px;border-radius:50%;background:var(--white)}
</style>
</head>
<body>

<header class="section site-header">
  <div class="brand"><span class="brand-dot"></span>Barkfeast</div>
  <nav class="main-nav">
    <span class="active">Home</span><span>Our Food</span><span>How It Works</span><span>Pricing</span><span>Customer Reviews</span><span>FAQ</span><span>Contact Us</span>
    <span class="login">Log In</span>
  </nav>
</header>

<section class="section hero">
  <div class="hero-photo" role="img" aria-label="Dog eating from a steel bowl"></div>
  <h1>Food unique as your dog blended using the<br>finest ingredients</h1>
  <span class="btn btn-solid">Tell us about your dog</span>
  <div class="play">
    <svg width="20" height="20" viewBox="0 0 20 20"><circle cx="10" cy="10" r="10" fill="#fff"/><path d="M8 6l6 4-6 4z" fill="#555"/></svg>
    Play Video
  </div>
  <div class="dots"><span></span><span></span><span></span><span></span></div>
</section>

<section class="section how">
  <h2 class="section-title">How It Works</h2>
  <div class="steps">
    <div class="step">
      <svg width="80" height="90" viewBox="0 0 80 90" fill="none" stroke="#e8912c" stroke-width="2.5"><rect x="14" y="10" width="52" height="72" rx="4"/><rect x="28" y="4" width="24" height="12" rx="3"/><circle cx="40" cy="48" r="14"/><path d="M24 72h32"/></svg>
      <h3>Tell About Your Dog</h3>
      <p>Share the breed, age, weight and habits of your dog so we can plan the right daily meal.</p>
    </div>
    <div class="step">
      <svg width="80" height="90" viewBox="0 0 80 90" fill="none" stroke="#e8912c" stroke-width="2.5"><path d="M16 10h40l8 10v62H16z"/><circle cx="46" cy="58" r="16"/><path d="M38 58l6 6 10-12"/><path d="M24 26h24M24 36h18"/></svg>
      <h3>We Create Your Food</h3>
      <p>Our team blends a recipe with the finest ingredients matched to your dog's needs.</p>
    </div>
    <div class="step">
      <svg width="90" height="90" viewBox="0 0 90 90" fill="none" stroke="#e8912c" stroke-width="2.5"><rect x="40" y="14" width="36" height="30" rx="2"/><path d="M58 14v30"/><circle cx="28" cy="40" r="9"/><path d="M14 80c0-16 6-26 14-26s14 10 14 26"/><path d="M42 62h30"/></svg>
      <h3>We Deliver</h3>
      <p>Fresh packs arrive at your door on a schedule that suits you and your dog.</p>
    </div>
  </div>
</section>

<section class="section food-row grey" style="top:1145px">
  <div class="food-photo" role="img" aria-label="Bowl of dry dog kibble on a wooden table" style="background:linear-gradient(135deg,#6a4028,#8c5a34 55%,#5a3520)"></div>
  <div class="food-text">
    <h2>Our Foods</h2>
    <p>We develop and create your dogs ideal food using the finest ingredients, based on your dogs requirements.</p>
    <p>Our foods are developed by pet nutritionists, approved by vets and enjoyed by all dogs.</p>
    <span class="btn">Start Now</span>
  </div>
</section>

<section class="section food-row reverse" style="top:1484px">
  <div class="food-photo" role="img" aria-label="Senior dog eating from a bowl on a kitchen floor" style="background:linear-gradient(135deg,#ddd6ca,#a88a68 60%,#7a5e44)"></div>
  <div class="food-text">
    <h2>Senior Food</h2>
    <p>The right balance of protein and energy to help reduce joint pain, while maintaining weight to keep your dog active.</p>
    <span class="btn">Tell Me More</span>
  </div>
</section>

<section class="section food-row grey" style="top:1821px">
  <div class="food-photo" role="img" aria-label="Labrador waiting beside an owner holding a food bowl" style="background:linear-gradient(135deg,#8a5050,#c8a070 55%,#e6ddd0)"></div>
  <div class="food-text">
    <h2>Adult Food</h2>
    <p>Careful balance of proteins, fats and oils, minerals, vitamins and carbohydrates are needed as an adult and differ between breeds.</p>
    <span class="btn">Tell Me More</span>
  </div>
</section>

<section class="section food-row reverse" style="top:2157px">
  <div class="food-photo" role="img" aria-label="Puppies eating from a bowl on a lawn" style="background:linear-gradient(135deg,#9a6434,#a8703a 55%,#7a7a3a)"></div>
  <div class="food-text">
    <h2>Puppy Food</h2>
    <p>A well balanced and nutritious range of foods to meet the needs of growing puppies of all breeds.</p>
    <span class="btn">Start Now</span>
  </div>
</section>

<section class="section food-row grey" style="top:2497px">
  <div class="food-photo" role="img" aria-label="Dog looking at a hand holding a bowl of food" style="background:linear-gradient(135deg,#222,#3a2c22 55%,#a07a48)"></div>
  <div class="food-text">
    <h2>Foods for Health Problems</h2>
    <p>Itchy Skin?<br>Joint Problems ? Sensitive tummy?<br>We will create a food to suit your dogs needs</p>
    <span class="btn">Start Now</span>
  </div>
</section>

<section class="section food-row reverse" style="top:2837px">
  <div class="food-photo" role="img" aria-label="Scoop of kibble poured into a bowl" style="background:linear-gradient(135deg,#d4cdc2,#a89a82 55%,#6e8a48)"></div>
  <div class="food-text">
    <h2>Weight Control Food</h2>
    <p>Weight control is about still giving your dog a filling and tasty food that will satisfy your dogs appetite whilst keeping off extra weight.</p>
    <span class="btn">Tell Me More</span>
  </div>
</section>

<section class="section food-row grey" style="top:3173px">
  <div class="food-photo" role="img" aria-label="Orange bowl overflowing with dry dog food" style="background:linear-gradient(135deg,#f2eee8,#e08a36 55%,#b0602a)"></div>
  <div class="food-text">
    <h2>Specialist Foods</h2>
    <p>We provide grain free and hypoallergenic foods for fussy eaters, dogs with allergies and food intolerances.</p>
    <span class="btn">Tell Me More</span>
  </div>
</section>

<section class="section reviews">
  <div class="kibble" role="img" aria-label="Scattered dog kibble"></div>
  <h2 class="section-title">What Our Customers Say</h2>
  <svg class="arrow" style="left:195px" width="24" height="40" viewBox="0 0 24 40"><path d="M20 4L6 20l14 16" fill="none" stroke="#666" stroke-width="4"/></svg>
  <div class="review-card">
    <div class="avatar" role="img" aria-label="Customer holding his dog"></div>
    <blockquote>" I have 3 dogs all on different foods. No more trips to the shops fetching massive bags of food. This works for me and my dogs love it.."</blockquote>
    <cite>-Harold - Oldham</cite>
  </div>
  <svg class="arrow" style="left:980px" width="24" height="40" viewBox="0 0 24 40"><path d="M4 4l14 16L4 36" fill="none" stroke="#666" stroke-width="4"/></svg>
  <span class="btn">View All Testimonials</span>
</section>

<section class="section faq">
  <h2 class="section-title">FAQ</h2>
  <ul class="faq-list">
    <li>Maecenas scelerisque posuere tellus eget lacinia convallis vestibulum nisi eget?<span>›</span></li>
    <li>uis ultricies nisl vitae tellus feugiat, sit amet porta metus ornare?<span>›</span></li>
    <li>Maecenas scelerisque posuere tellus eget lacinia convallis vestibulum nisl egetuis ultricies nisl vitae tellus feugiat<span>›</span></li>
    <li>Maecenas scelerisqueuis ultricies nisl vitae tellus feugiat, sit amet porta metus ornare<span>›</span></li>
    <li>Maecenas scelerisque posuere tellus ?<span>›</span></li>
  </ul>
</section>

<section class="section contact">
  <div class="contact-kibble" role="img" aria-label="Pile of dog kibble"></div>
  <div class="contact-dog" role="img" aria-label="Small black and white dog beside a red food bowl"></div>
  <h2 class="section-title">Contact Form</h2>
  <div class="contact-form">
    <div class="field-row"><div class="field">Name</div><div class="field">Email Address</div></div>
    <div class="field-row"><div class="field">Phone No</div><div class="field">Subject</div></div>
    <div class="field message">Message</div>
    <span class="btn btn-solid">Submit</span>
  </div>
</section>

<footer class="section site-footer">
  <nav class="footer-nav"><span>Home</span><span>Our Food</span><span>How It Works</span><span>Pricing</span><span>Customer Reviews</span><span>FAQ</span><span>Contact Us</span></nav>
  <p class="copyright">© Copyright 2018 Company Name All Rights Reserved.</p>
  <div class="social"><span></span><span></span></div>
</footer>

</body>
</html>
```